Stylish Business Cards Wanted

- DOUBLE SIDED Design Required -

High end, edgy cards for a corporate and personal stylist. Must include logo,
Name: Belinda Harwick
Title: Director and Stylist
telephone : +61 8 7142 5809
email: belinda@theloombriefing.example
website: theloombriefing.example
Tag: Corporate Workwear & Uniform Specialist | Personal Stylist
Would like nice icons for telephone, email, website

Target Market(s)

Businesses wanting stylish uniforms, people wanting stylish wardrobes

Industry/Entity Type

Corporate Workwear Stylist

Contact Information for Business Card

I would like black, white and gold foiling incorporated in the design - possibly a touch of the other colours on my branding guide attached Name: Belinda Harwick Title: Director and Stylist telephone : +61 8 7142 5809 email: belinda@theloombriefing.example website: theloombriefing.example Tag: Corporate Workwear & Uniform Specialist | Personal Stylist Would like nice icons for telephone, email, website

Font styles to use
Other font styles liked:
• Raleway

Colors

Designer to choose colors to be used in the design.

Requirements
Must have
• Gold foil accents

```html
<!DOCTYPE html>
<html lang="en">
<head>
<meta charset="utf-8">
<title>The Loom Briefing – Business Cards</title>
<link href="https://fonts.googleapis.com/css2?family=Raleway:wght@300;400;600;700&display=swap" rel="stylesheet">
<style>
  :root {
    --backdrop: #e9e4de;
    --card-white: #ffffff;
    --card-black: #202020;
    --ink: #333333;
    --text-light: #f2f2f2;
    --text-soft: #d8d8d8;
    --gold: #d6ac3c;
    --watermark: #2c2c2c;
    --shadow: rgba(0, 0, 0, 0.28);
  }
  * { box-sizing: border-box; margin: 0; padding: 0; }
  html, body {
    width: 1200px;
    height: 863px;
    overflow: hidden;
    background: var(--backdrop);
    font-family: "Raleway", Arial, sans-serif;
  }
  .sheet {
    position: relative;
    width: 1200px;
    height: 863px;
    display: flex;
    justify-content: center;
    align-items: center;
    gap: 60px;
  }
  .card {
    position: relative;
    width: 340px;
    height: 550px;
    border-radius: 4px;
    box-shadow: 0 12px 28px var(--shadow);
    overflow: hidden;
  }
  /* Front */
  .card--front { background: var(--card-white); }
  .brand-mark {
    position: absolute;
    right: 34px;
    bottom: 46px;
    text-align: right;
    font-weight: 700;
    font-size: 30px;
    line-height: 1.05;
    color: var(--ink);
    letter-spacing: 0.5px;
  }
  /* Back */
  .card--back { background: var(--card-black); color: var(--text-light); }
  .contact-block {
    position: absolute;
    top: 42px;
    left: 30px;
    right: 24px;
  }
  .person-name {
    font-weight: 700;
    font-size: 24px;
    color: var(--text-light);
    letter-spacing: 0.3px;
  }
  .person-title {
    margin-top: 3px;
    font-weight: 600;
    font-size: 12px;
    color: var(--gold);
  }
  .contact-list {
    list-style: none;
    margin-top: 20px;
  }
  .contact-item {
    display: flex;
    align-items: center;
    gap: 9px;
    font-size: 11.5px;
    font-weight: 400;
    color: var(--text-soft);
    margin-bottom: 9px;
  }
  .contact-icon { width: 13px; height: 13px; flex: none; }
  .brand-watermark {
    position: absolute;
    left: 0;
    right: 0;
    top: 215px;
    text-align: center;
    font-weight: 700;
    font-size: 52px;
    line-height: 1.05;
    color: var(--watermark);
  }
  .tagline {
    position: absolute;
    left: 30px;
    right: 24px;
    bottom: 36px;
    font-weight: 300;
    font-size: 14px;
    line-height: 1.35;
    color: var(--text-light);
  }
</style>
</head>
<body>
<main class="sheet">
  <section class="card card--front" aria-label="Card front">
    <div class="brand-mark">The Loom<br>Briefing</div>
  </section>

  <section class="card card--back" aria-label="Card back">
    <div class="brand-watermark" aria-hidden="true">The Loom<br>Briefing</div>

    <div class="contact-block">
      <h1 class="person-name">Belinda Harwick</h1>
      <p class="person-title">Director and Stylist</p>
      <ul class="contact-list">
        <li class="contact-item">
          <svg class="contact-icon" viewBox="0 0 16 16" aria-hidden="true">
            <path fill="#f2f2f2" d="M3.6 1.5l2.2 2.6c.3.4.3.9 0 1.3L4.6 6.7c.9 2 2.6 3.7 4.6 4.6l1.3-1.2c.4-.3.9-.3 1.3 0l2.6 2.2c.4.4.4 1 0 1.4l-1.2 1.2c-.6.6-1.5.8-2.3.5C6.3 13.8 2.2 9.7.6 5.1.3 4.3.5 3.4 1.1 2.8L2.3 1.5c.4-.4 1-.4 1.3 0z"/>
          </svg>
          <span>+61 8 7142 5809</span>
        </li>
        <li class="contact-item">
          <svg class="contact-icon" viewBox="0 0 16 16" aria-hidden="true">
            <rect x="1" y="3" width="14" height="10" rx="1" fill="#f2f2f2"/>
            <path d="M1.5 3.8L8 9l6.5-5.2" fill="none" stroke="#202020" stroke-width="1.3"/>
          </svg>
          <span>belinda@theloombriefing.example</span>
        </li>
        <li class="contact-item">
          <svg class="contact-icon" viewBox="0 0 16 16" aria-hidden="true">
            <circle cx="8" cy="8" r="7" fill="#f2f2f2"/>
            <g fill="none" stroke="#202020" stroke-width="1">
              <ellipse cx="8" cy="8" rx="3" ry="6.5"/>
              <path d="M1.5 8h13M2.6 4.8h10.8M2.6 11.2h10.8"/>
            </g>
          </svg>
          <span>theloombriefing.example</span>
        </li>
      </ul>
    </div>

    <p class="tagline">Corporate Workwear &amp;<br>Uniform Specialist | Personal Stylist</p>
  </section>
</main>
</body>
</html>
```